Specialised investor in e-mobility and energy wants business card design

We need a business card design that fits our existing corporate design. <The look and feel must be 'sharp'/'clean', dynamic, communicate momentum, professionalism etc (as one would imagine from a firm in the financial sector). We like the idea of a reverse-side of the card that includes the logo, and the name and contact details on the other. We expect the deliverable to be whatever format might be required to be able to get cards printed directly by a service such as kelmo press. Our website is www.zub.capital

```html
<!DOCTYPE html>
<html lang="en">
<head>
<meta charset="utf-8">
<title>Zub Capital – Business Card</title>
<link href="https://fonts.googleapis.com/css2?family=Lato:wght@400;700;900&display=swap" rel="stylesheet">
<style>
  :root {
    --bg: #1c1c1c;
    --green-dark: #325026;
    --green-light: #86b64b;
    --white: #ffffff;
    --card-w: 700px;
    --card-h: 400px;
  }
  * { box-sizing: border-box; margin: 0; padding: 0; }
  html, body { width: 1200px; height: 1122px; overflow: hidden; }
  body {
    background: var(--bg);
    font-family: 'Lato', sans-serif;
    display: flex;
    flex-direction: column;
    align-items: center;
    justify-content: center;
    gap: 70px;
  }
  .card {
    width: var(--card-w);
    height: var(--card-h);
    border-radius: 22px;
    background: var(--white);
    position: relative;
    overflow: hidden;
  }
  .wordmark {
    font-family: 'Lato', sans-serif;
    font-weight: 400;
    color: var(--green-dark);
    display: flex;
    align-items: center;
    gap: 14px;
    white-space: nowrap;
  }
  .wordmark .mark-square {
    width: 0.5em; height: 0.5em;
    background: var(--green-dark);
  }
  .card-front { display: flex; align-items: center; justify-content: center; }
  .card-front .wordmark { font-size: 72px; }

  .card-back .shape-layer { position: absolute; inset: 0; }
  .card-back .wordmark {
    position: absolute;
    left: 400px; top: 150px;
    font-size: 40px;
  }
  .contact-block {
    position: absolute;
    left: 60px; top: 120px;
    color: var(--white);
  }
  .person-name {
    font-weight: 900;
    font-size: 30px;
    letter-spacing: 0.5px;
    line-height: 1;
  }
  .person-role {
    color: var(--green-light);
    font-weight: 700;
    font-size: 19px;
    margin-top: 6px;
  }
  .contact-list { list-style: none; margin-top: 22px; }
  .contact-list li {
    display: flex;
    align-items: flex-start;
    gap: 12px;
    font-size: 15px;
    line-height: 1.45;
    margin-bottom: 4px;
  }
  .contact-list svg { flex: none; width: 15px; height: 15px; margin-top: 3px; }
</style>
</head>
<body>

  <section class="card card-front">
    <div class="wordmark"><span class="mark-square"></span>Zub Capital</div>
  </section>

  <section class="card card-back">
    <svg class="shape-layer" viewBox="0 0 700 400" preserveAspectRatio="none" aria-hidden="true">
      <polygon points="0,0 320,0 345,400 0,400" fill="var(--green-dark)"/>
      <polygon points="655,0 700,0 700,400 670,400" fill="var(--green-light)"/>
    </svg>

    <div class="contact-block">
      <div class="person-name">ARON VELSKY</div>
      <div class="person-role">Founder &amp; CEO</div>
      <ul class="contact-list">
        <li>
          <svg viewBox="0 0 16 16"><path d="M8 1a5 5 0 0 0-5 5c0 4 5 9 5 9s5-5 5-9a5 5 0 0 0-5-5zm0 7a2 2 0 1 1 0-4 2 2 0 0 1 0 4z" fill="var(--green-light)"/></svg>
          <span>Zub Capital S.A.<br>Geneva, Switzerland</span>
        </li>
        <li>
          <svg viewBox="0 0 16 16"><rect x="4" y="1" width="8" height="14" rx="1.5" fill="none" stroke="var(--green-light)" stroke-width="1.6"/><circle cx="8" cy="12.5" r="0.9" fill="var(--green-light)"/></svg>
          <span>+41 79555 0184</span>
        </li>
        <li>
          <svg viewBox="0 0 16 16"><rect x="1" y="3" width="14" height="10" rx="1" fill="var(--green-light)"/><path d="M1.5 3.8 8 9l6.5-5.2" fill="none" stroke="var(--green-dark)" stroke-width="1.2"/></svg>
          <span>aron@zub.capital</span>
        </li>
        <li>
          <svg viewBox="0 0 16 16"><circle cx="8" cy="8" r="6.5" fill="none" stroke="var(--green-light)" stroke-width="1.6"/><path d="M1.5 8h13M8 1.5c-2.5 3-2.5 10 0 13M8 1.5c2.5 3 2.5 10 0 13" fill="none" stroke="var(--green-light)" stroke-width="1.1"/></svg>
          <span>www.zub.capital</span>
        </li>
      </ul>
    </div>

    <div class="wordmark"><span class="mark-square"></span>Zub Capital</div>
  </section>

</body>
</html>
```